πΈ Full Website Redesign on Wix β The Willowmere Atelier (Feminine, Sophisticated, Nature-Inspired)
Business Name: The Willowmere Atelier
Current Site: https://quorvalen.example/Tz8pLmQ (for structure reference only)
Platform: Wix
Business Type: Women-led Canadian online retail business
Location: Canada
π About The Willowmere Atelier
The Willowmere Atelier is a boutique e-commerce store specializing in roses and blooming plants, created for modern plant lovers who appreciate beauty, quality, and storytelling.
We are a small, women-led business in Ontario, Canada, and our audience is primarily women who are drawn to floral aesthetics, a calming user experience, and elevated design.
Our name β The Willowmere Atelier β represents both a curated collection of blooms and a love of thoughtful, meaningful beauty.
π» Project Overview
We are looking for a full website redesign from scratch (built on Wix) that reflects our brand identity: feminine, sophisticated, romantic, and grounded in nature.
The current version of the site was just a test layout β we now want a fresh, cohesive design vision that speaks directly to our female Canadian customer base with a clean, modern, and elegant interface.
This project is not just about functionality β itβs about crafting an experience that feels like a digital floral sanctuary.
π― What We Need
Full website design and development in Wix (you can start fresh)
Custom homepage design with storytelling and a welcoming brand vibe
Pages to include (subject to refinement):
Home
Shop (products will be added by us later)
About
Contact
FAQ / Info
Blog or Guides (optional placeholder)
Sophisticated visual branding:
Muted rose, blush, and earthy tones
Clean, modern layout with elegant typography
Feminine, natural, soft design elements (think floral details, soft lines, minimalism with warmth)
Optimized for both desktop and mobile
Set up global styles (font, color palette, button styles, etc.)
Guidance or setup for product sections using Wixβs eCommerce system
Create beautiful reusable sections (for us to duplicate later as needed)
π· Brand Style
We are aiming for a website that feels like:
A curated botanical boutique
Feminine and warm β but not overly girly
Sophisticated and soft, never cluttered
Clean but not sterile
Relaxed elegance with a focus on natural beauty
Color palette:
Muted rose
Warm blush tones
Cream, soft beige, earthy sage
Very subtle contrast β no stark black-and-white
Typography:
Elegant serif or soft sans-serif pairings
Easy to read but with character
π Technical Info
Platform: Wix
No custom coding required (Wix-native tools preferred)
We will handle product uploads
Weβll provide any imagery you request
π¦ Deliverables
Fully designed Wix website (ready to publish)
All pages complete with consistent design and layout
Mobile-responsive layout
Design system set up for future content (colors, typography, etc.)
Optional: Style guide PDF for brand reference (bonus)
π Timeline
Weβd like the website to be completed within 1-2 weeks after project start. Please let us know your availability.
β
To Apply
Please include:
Portfolio (especially if youβve done Wix, floral, feminine, or nature-inspired work)
A short message on how you'd approach this project
Timeline/availability
We're looking for someone who understands how to design for emotion, beauty, and ease β not just functionality. If you love soft colors, delicate details, and creating meaningful digital experiences for women, we'd love to hear from you.
πΈ Letβs build something beautiful together!
Rose enthusiasts

```html
<!DOCTYPE html>
<html lang="en">
<head>
<meta charset="utf-8">
<title>The Willowmere Atelier</title>
<link rel="stylesheet" href="https://fonts.googleapis.com/css2?family=Cormorant+Garamond:wght@500;600&family=Quicksand:wght@400;500;600&display=swap">
<style>
:root{
  --rose:#c08a85;
  --rose-deep:#b37a76;
  --cream:#faf6f2;
  --beige:#efe6dd;
  --beige-deep:#e8ddd2;
  --ink:#4a3c39;
  --muted:#6a5b57;
  --white:#ffffff;
}
*{box-sizing:border-box;margin:0;padding:0}
html,body{width:1200px;height:3638px;overflow:hidden}
body{position:relative;background:var(--cream);font-family:"Quicksand",sans-serif;color:var(--ink)}
.abs{position:absolute}
.serif{font-family:"Cormorant Garamond",serif}
.heading{font-family:"Cormorant Garamond",serif;font-weight:500;color:var(--rose-deep);text-transform:uppercase;letter-spacing:.5px}
.btn{position:absolute;background:var(--rose);color:var(--white);font-size:13px;font-weight:600;text-transform:uppercase;display:flex;align-items:center;justify-content:center;border-radius:3px;letter-spacing:.2px}
.band{position:absolute;left:0;width:1200px;background:var(--beige)}
.photo{position:absolute}
.center{text-align:center}
.body-text{font-size:14.5px;line-height:31px;color:var(--muted)}

/* header */
.brand{left:112px;top:22px;display:flex;align-items:center;gap:14px}
.brand-mark{width:34px;height:44px;background:var(--rose);border-radius:3px}
.brand-name{font-family:"Cormorant Garamond",serif;font-weight:600;color:var(--rose);font-size:17px;text-transform:uppercase}
.nav{top:34px;left:467px;display:flex;gap:0;font-size:14px;font-weight:500;text-transform:uppercase}
.nav span{margin-right:38px}
.nav .active{color:var(--rose)}
.login{left:1000px;top:29px;width:88px;height:32px;border:1px solid var(--rose);border-radius:4px;color:var(--rose);font-size:13px;display:flex;align-items:center;justify-content:center;gap:8px;background:var(--white)}

/* dot grids */
.dots{background-image:radial-gradient(circle,var(--ink) 1.2px,transparent 1.6px);background-size:12px 12px}

/* cards */
.card-name{font-family:"Cormorant Garamond",serif;font-weight:500;font-size:23px;width:315px;text-align:center}
.card-price{font-size:19px;font-weight:600;color:var(--rose);width:315px;text-align:center}

.foot-nav{top:3534px;left:374px;display:flex;font-size:14px;text-transform:uppercase}
.foot-nav span{margin-right:38px}
</style>
</head>
<body>

<!-- Header -->
<div class="abs brand"><div class="brand-mark"></div><div class="brand-name">The Willowmere Atelier</div></div>
<nav class="abs nav"><span class="active">Home</span><span>Shop</span><span>About</span><span>FAQ</span><span>Blog</span><span>Contact</span></nav>
<div class="abs login">
  <svg width="11" height="12" viewBox="0 0 11 12"><circle cx="5.5" cy="3.2" r="2.8" fill="#c08a85"/><path d="M0 12c0-4 2.5-5.5 5.5-5.5S11 8 11 12z" fill="#c08a85"/></svg>LOGIN
</div>

<!-- Hero -->
<div class="photo" role="img" aria-label="Hands holding a leafy green potted plant" style="left:108px;top:89px;width:284px;height:373px;background:linear-gradient(150deg,#efece7,#3d4a33 55%,#c9b9a8)"></div>
<div class="photo" role="img" aria-label="Smiling woman holding two potted plants in a greenhouse" style="left:442px;top:89px;width:650px;height:373px;background:linear-gradient(110deg,#3e5a36,#7f9a6e 45%,#c7ad97 70%,#4e6a44)"></div>
<svg class="abs" style="left:370px;top:130px" width="450" height="292" viewBox="0 0 450 292">
  <polygon points="0,0 340,0 400,146 340,292 0,292" fill="#efe6dd"/>
  <polygon points="340,0 380,0 442,146 380,292 340,292 400,146" fill="#c08a85"/>
</svg>
<div class="abs heading" style="left:400px;top:156px;width:345px;font-size:24px;line-height:39px">Potted beauty, ready to root at home</div>
<div class="abs" style="left:400px;top:242px;width:290px;font-size:14px;line-height:28.5px;color:var(--muted)">Modern botanical beauty, thoughtfully designed for women who love nature and elegance.</div>
<div class="btn" style="left:400px;top:349px;width:290px;height:38px">Browse roses &amp; blooming plants</div>

<!-- Mission band -->
<div class="band" style="top:545px;height:445px"></div>
<div class="abs heading center" style="left:0;top:592px;width:1200px;font-size:30px">Where blooms meet meaning</div>
<div class="abs" style="left:600px;top:645px;width:1px;height:40px;background:var(--rose)"></div>
<div class="abs body-text center" style="left:140px;top:700px;width:920px;font-size:14px;line-height:32px">The Willowmere Atelier is your one-stop destination for high-quality roses and blooming plants. We are dedicated to bringing the beauty of nature to your doorstep. Our story is rooted in a passion for plants and a commitment to providing exceptional service to our customers. Join us on this botanical journey, and let's explore the world of roses and blooming plants together</div>
<div class="abs body-text center" style="left:160px;top:806px;width:880px;font-size:14px;line-height:32px">Our mission is to connect people with the beauty and serenity of nature through our carefully curated selection of roses and blooming plants.</div>
<div class="btn" style="left:518px;top:897px;width:164px;height:39px">Get started now</div>

<!-- Journey -->
<div class="abs dots" style="left:84px;top:1050px;width:86px;height:92px;clip-path:polygon(0 0,100% 0,100% 14%,14% 14%,14% 100%,0 100%)"></div>
<div class="photo" style="left:447px;top:1072px;width:126px;height:473px;background:var(--rose);clip-path:polygon(0 0,46% 0,100% 50%,46% 100%,0 100%)"></div>
<div class="photo" role="img" aria-label="Woman in a sun hat holding a wrapped rubber plant" style="left:112px;top:1072px;width:393px;height:473px;background:linear-gradient(160deg,#ece4da,#c98a5c 55%,#a5684a);clip-path:polygon(0 0,85% 0,100% 50%,85% 100%,0 100%)"></div>
<div class="abs heading" style="left:673px;top:1068px;width:440px;font-size:30px;line-height:52px">Our journey from seed to blossom</div>
<div class="abs body-text" style="left:673px;top:1175px;width:420px;font-size:14px">The Willowmere Atelier is dedicated to providing a curated collection of roses and blooming plants, carefully selected to bring joy and elegance to your home garden. Our team is committed to sharing our passion for plants and fostering a community of plant enthusiasts. Join us in celebrating the beauty of nature and the art of plant care.</div>
<div class="abs body-text" style="left:673px;top:1373px;width:435px;font-size:14px">The Willowmere Atelier is your one-stop destination for high quality roses and blooming plants. We are dedicated to bringing the beauty of nature to your doorstep.</div>
<div class="btn" style="left:674px;top:1496px;width:134px;height:39px">Our mission</div>
<div class="photo" role="img" aria-label="Soft pale blossoms fading into the background" style="left:830px;top:1440px;width:370px;height:188px;background:radial-gradient(ellipse at 85% 80%,#f1e3e0,rgba(250,246,242,0) 70%)"></div>

<!-- Collection -->
<div class="band" style="top:1628px;height:567px"></div>
<div class="abs heading center" style="left:0;top:1678px;width:1200px;font-size:30px">Explore the collection</div>

<div class="photo" style="left:340px;top:1766px;width:87px;height:199px;background:var(--rose);clip-path:polygon(0 0,35% 0,100% 50%,35% 100%,0 100%)"></div>
<div class="photo" role="img" aria-label="Bush of golden-orange roses" style="left:112px;top:1766px;width:270px;height:199px;background:linear-gradient(140deg,#3c5a2c,#e7a43a 45%,#4f6b33);clip-path:polygon(0 0,88% 0,100% 50%,88% 100%,0 100%)"></div>
<div class="abs card-name" style="left:76px;top:1992px">Amber Meadow</div>
<div class="abs card-price" style="left:76px;top:2034px">C$31.99</div>

<div class="photo" style="left:674px;top:1766px;width:87px;height:199px;background:var(--rose);clip-path:polygon(0 0,35% 0,100% 50%,35% 100%,0 100%)"></div>
<div class="photo" role="img" aria-label="Close-up of a coral-orange rose" style="left:446px;top:1766px;width:270px;height:199px;background:radial-gradient(circle at 50% 50%,#f7a06a,#e56a3a 55%,#5a6b3a);clip-path:polygon(0 0,88% 0,100% 50%,88% 100%,0 100%)"></div>
<div class="abs card-name" style="left:433px;top:1992px">Coral Whisper</div>
<div class="abs card-price" style="left:433px;top:2034px">C$31.99</div>

<div class="photo" style="left:1007px;top:1766px;width:87px;height:199px;background:var(--rose);clip-path:polygon(0 0,35% 0,100% 50%,35% 100%,0 100%)"></div>
<div class="photo" role="img" aria-label="Soft yellow roses among blue garden flowers" style="left:780px;top:1766px;width:270px;height:199px;background:linear-gradient(130deg,#5f7d4a,#f2df6a 55%,#3e5a30);clip-path:polygon(0 0,88% 0,100% 50%,88% 100%,0 100%)"></div>
<div class="abs card-name" style="left:770px;top:1992px">Golden Verse</div>
<div class="abs card-price" style="left:770px;top:2034px">C$34.00</div>

<div class="btn" style="left:496px;top:2099px;width:208px;height:39px">View more collection</div>

<!-- Testimonials -->
<div class="abs heading center" style="left:0;top:2264px;width:1200px;font-size:30px">Client success stories</div>
<div class="photo" role="img" aria-label="Woman smelling a bouquet of pink flowers" style="left:0;top:2340px;width:248px;height:270px;background:radial-gradient(ellipse at 40% 50%,#e9c9c4,#f3e5e2 55%,rgba(250,246,242,0) 75%)"></div>
<div class="abs serif" style="left:155px;top:2290px;font-size:110px;color:#e6dcd6;line-height:1">&ldquo;</div>
<div class="abs center" style="left:170px;top:2331px;width:860px;font-size:14px;line-height:31px;color:var(--muted)">"The Willowmere Atelier isn't just an online flower shop — it feels like stepping into a sanctuary of beauty. Every rose I've received is chosen with such care and elegance, wrapped like a gift meant only for me. Supporting a women-led Canadian brand that puts heart into every detail makes each bouquet feel even more meaningful. It's not just about flowers, it's about the story they carry into my home."</div>
<div class="abs center" style="left:0;top:2474px;width:1200px;font-size:16px;font-weight:600;color:var(--muted);text-transform:uppercase">Marielle T., Vancouver</div>
<svg class="abs" style="left:566px;top:2522px" width="68" height="12"><circle cx="8" cy="6" r="4.5" fill="none" stroke="#c08a85"/><circle cx="34" cy="6" r="4.5" fill="#c08a85"/><circle cx="60" cy="6" r="4.5" fill="none" stroke="#c08a85"/></svg>

<!-- Blog -->
<div class="abs dots" style="left:1026px;top:2568px;width:86px;height:92px;clip-path:polygon(0 0,100% 0,100% 100%,86% 100%,86% 14%,0 14%)"></div>
<div class="photo" style="left:545px;top:2587px;width:150px;height:335px;background:var(--rose);clip-path:polygon(0 50%,42% 0,100% 0,100% 100%,42% 100%)"></div>
<div class="photo" role="img" aria-label="Florist handing a bouquet to a customer in a plant shop" style="left:618px;top:2587px;width:472px;height:335px;background:linear-gradient(120deg,#6e4a38,#4f6a43 40%,#b98a6a 70%,#7a3b38);clip-path:polygon(0 50%,12% 0,100% 0,100% 100%,12% 100%)"></div>
<div class="abs heading" style="left:112px;top:2634px;width:380px;font-size:30px;line-height:52px">The bloom guide:<br>our plant care blog</div>
<div class="abs" style="left:112px;top:2755px;font-size:17px;color:var(--ink)">Your Source for Plant Care Tips and Advice</div>
<div class="btn" style="left:113px;top:2817px;width:237px;height:39px">Read our latest articles</div>

<!-- Newsletter -->
<div class="band" style="top:2988px;height:142px;background:var(--beige-deep)"></div>
<div class="abs heading" style="left:112px;top:3018px;font-size:24px;line-height:45px">Stay informed about plants and more.<br>No spam, we promise.</div>
<div class="abs" style="left:730px;top:3039px;width:358px;height:37px;background:var(--white);border-radius:3px"></div>
<div class="abs serif" style="left:745px;top:3049px;font-size:14px;font-weight:600;text-transform:uppercase;color:var(--ink)">Email address</div>
<div class="btn" style="left:977px;top:3044px;width:105px;height:26px;font-size:11px">Subscribe us</div>

<!-- Community feed -->
<div class="abs heading center" style="left:0;top:3198px;width:1200px;font-size:30px">Join our Garden Circle</div>
<div class="abs" style="left:112px;top:3293px;width:976px;height:203px;background:var(--beige-deep);border-radius:8px"></div>
<div class="abs" style="left:112px;top:3293px;width:38px;height:203px;display:flex;align-items:center;justify-content:center"><span style="transform:rotate(-90deg);white-space:nowrap;font-size:13px;font-weight:600;text-transform:uppercase">Follow me</span></div>
<div class="photo" role="img" aria-label="Two women looking at a tablet among plants" style="left:167px;top:3293px;width:205px;height:203px;background:linear-gradient(135deg,#c7a28a,#6a7a55 60%,#e7e0d6)"></div>
<div class="photo" role="img" aria-label="Bust sculpture and green vase on a wooden cabinet" style="left:387px;top:3293px;width:203px;height:203px;background:linear-gradient(180deg,#f2f0ec 45%,#7a4a2a)"></div>
<div class="photo" role="img" aria-label="Small potted tree beside a wooden easel" style="left:608px;top:3293px;width:205px;height:203px;background:linear-gradient(180deg,#ebe6df,#cbb79c 70%,#e9e2d8)"></div>
<div class="photo" role="img" aria-label="Garden tools and scissors on a woven surface" style="left:828px;top:3293px;width:205px;height:203px;background:linear-gradient(135deg,#8a6a4e,#c9a98a 50%,#6e5440)"></div>
<div class="abs" style="left:330px;top:3303px;width:28px;height:28px;background:var(--white);border-radius:5px"></div>
<div class="abs" style="left:550px;top:3303px;width:28px;height:28px;background:var(--white);border-radius:5px"></div>
<div class="abs" style="left:771px;top:3303px;width:28px;height:28px;background:var(--white);border-radius:5px"></div>
<div class="abs" style="left:991px;top:3303px;width:28px;height:28px;background:var(--white);border-radius:5px"></div>
<svg class="abs" style="left:1060px;top:3322px" width="16" height="150"><circle cx="8" cy="8" r="6" fill="#4a3c39"/><circle cx="8" cy="72" r="6" fill="#4a3c39"/><circle cx="8" cy="136" r="6" fill="#4a3c39"/></svg>

<!-- Footer -->
<nav class="abs foot-nav"><span>Home</span><span>Shop</span><span>About</span><span>FAQ</span><span>Blog</span><span>Contact</span></nav>
<div class="band" style="top:3600px;height:38px;background:var(--beige-deep)"></div>
<svg class="abs" style="left:580px;top:3584px" width="40" height="17"><polygon points="0,17 20,0 40,17" fill="#e8ddd2"/></svg>
<div class="abs center" style="left:0;top:3613px;width:1200px;font-size:11.5px;font-weight:500;text-transform:uppercase">Copyright © 2025 The Willowmere Atelier · All rights reserved</div>

</body>
</html>
```